Bluecrest Learning Corps by graduating students from college in two years

Based on the logo design, create stationary and business cards for
Dr. Venrel T Oskamp, CEO, (703) 482-1736
and Marisa Deltoft, Respresentative, (301) 647-2208
Address: 4719 Pellham Court, Harlow Ridge, VA 22187
Incorporate elelments of the logo

Target Market(s)

USA

Font styles to use
Other font styles liked:
• match with the logo type style

```html
<!DOCTYPE html>
<html lang="en">
<head>
<meta charset="utf-8">
<title>Bluecrest Learning Corps – Business Cards</title>
<link href="https://fonts.googleapis.com/css2?family=Open+Sans:wght@400;700&display=swap" rel="stylesheet">
<style>
  :root {
    --navy: #13296b;
    --navy-light: #23408a;
    --gold: #f6c636;
    --white: #ffffff;
    --grey-text: #5a5f6b;
    --backdrop: #333333;
  }
  * { box-sizing: border-box; margin: 0; padding: 0; }
  html, body { width: 1200px; height: 780px; overflow: hidden; }
  body {
    background: var(--backdrop);
    font-family: "Open Sans", sans-serif;
    position: relative;
  }
  .card {
    position: absolute;
    top: 235px;
    width: 540px;
    height: 309px;
    border-radius: 22px;
    overflow: hidden;
  }
  .card-back {
    left: 30px;
    background: linear-gradient(135deg, var(--navy) 0%, var(--navy-light) 60%, var(--navy) 100%);
    display: flex;
    align-items: center;
    justify-content: center;
  }
  .card-front { left: 630px; background: var(--white); }

  .brand {
    display: flex;
    align-items: center;
    gap: 10px;
    font-family: "Open Sans", sans-serif;
    font-weight: 700;
    white-space: nowrap;
  }
  .brand-dot { width: 16px; height: 16px; border-radius: 50%; background: var(--gold); flex: none; }
  .card-back .brand { color: var(--white); font-size: 24px; }
  .card-front .brand {
    position: absolute; left: 34px; top: 140px;
    color: var(--navy); font-size: 17px;
  }

  .wave { position: absolute; inset: 0; width: 100%; height: 100%; }

  .contact-primary {
    position: absolute; right: 30px; top: 34px; text-align: right;
  }
  .person-name { font-weight: 700; color: var(--navy); font-size: 21px; line-height: 1.2; }
  .person-role { color: var(--grey-text); font-size: 13px; }
  .person-phone { color: var(--grey-text); font-size: 13px; display: flex; justify-content: flex-end; align-items: center; gap: 6px; }

  .contact-secondary {
    position: absolute; right: 30px; bottom: 22px; text-align: right; color: var(--white);
    font-size: 13px; line-height: 1.4;
  }
  .contact-secondary .person-name { color: var(--gold); font-size: 19px; }
  .contact-secondary .person-role,
  .contact-secondary .person-phone { color: var(--white); font-size: 13px; }
  .address { margin-top: 8px; }
  .phone-icon { width: 13px; height: 13px; fill: var(--gold); }
</style>
</head>
<body>
  <section class="card card-back" aria-label="Business card back">
    <div class="brand"><span class="brand-dot"></span>Bluecrest Learning Corps</div>
  </section>

  <section class="card card-front" aria-label="Business card front">
    <svg class="wave" viewBox="0 0 540 309" preserveAspectRatio="none" aria-hidden="true">
      <path d="M0,268 C170,262 255,240 305,180 C355,118 410,92 540,88 L540,104 C420,108 370,132 322,192 C272,254 180,276 0,280 Z" fill="var(--gold)"/>
      <path d="M0,284 C180,280 275,258 325,198 C375,138 425,112 540,108 L540,309 L0,309 Z" fill="var(--navy)"/>
    </svg>

    <div class="brand"><span class="brand-dot"></span>Bluecrest Learning Corps</div>

    <div class="contact-primary">
      <div class="person-name">Dr. Venrel T Oskamp</div>
      <div class="person-role">CEO</div>
      <div class="person-phone">
        <svg class="phone-icon" viewBox="0 0 24 24" aria-hidden="true"><path d="M6.6 10.8a15.1 15.1 0 0 0 6.6 6.6l2.2-2.2a1 1 0 0 1 1-.25 11.4 11.4 0 0 0 3.6.57 1 1 0 0 1 1 1V20a1 1 0 0 1-1 1A17 17 0 0 1 3 4a1 1 0 0 1 1-1h3.5a1 1 0 0 1 1 1c0 1.25.2 2.45.57 3.57a1 1 0 0 1-.25 1z"/></svg>
        (703) 482-1736
      </div>
    </div>

    <div class="contact-secondary">
      <div class="person-name">Marisa Deltoft</div>
      <div class="person-role">Respresentative</div>
      <div class="person-phone">
        <svg class="phone-icon" viewBox="0 0 24 24" aria-hidden="true"><path d="M6.6 10.8a15.1 15.1 0 0 0 6.6 6.6l2.2-2.2a1 1 0 0 1 1-.25 11.4 11.4 0 0 0 3.6.57 1 1 0 0 1 1 1V20a1 1 0 0 1-1 1A17 17 0 0 1 3 4a1 1 0 0 1 1-1h3.5a1 1 0 0 1 1 1c0 1.25.2 2.45.57 3.57a1 1 0 0 1-.25 1z"/></svg>
        (301) 647-2208
      </div>
      <div class="address">4719 Pellham Court<br>Harlow Ridge, VA 22187</div>
    </div>
  </section>
</body>
</html>
```